VENTURE CAPITAL GROUP BUSINESS CARD DESIGN

Venture Capital Group based in SF looking for a bold business card design. No trendy colour explosion, 3D effects etc. Just "simple" optical effects. Works on your brain, keeps your eye focused and sticks to your mind.
Target Market(s)
Technology startups
Industry/Entity Type
Venture Capital
Contact Information for Business Card
DESMOND WHITLAKE
MANAGING PARTNER
187 FENWORTH ST SAN FRANCISCO, CA 94187
415.555.0142 O
415.555.0147 F
415.555.0193 C
desmond@veldtmoorcapital.ventures

```html
<!DOCTYPE html>
<html lang="en">
<head>
<meta charset="utf-8">
<title>Veldtmoor Capital Group – Business Card</title>
<link href="https://fonts.googleapis.com/css2?family=Merriweather:wght@400;700&family=Lato:wght@400&display=swap" rel="stylesheet">
<style>
  :root {
    --backdrop: #ecebeb;
    --card: #ffffff;
    --green: #1f8a35;
    --green-light: #3fae4a;
    --ink: #5a5a5a;
    --ink-soft: #6e6e6e;
    --disc: #eeeeee;
    --disc-edge: #dcdcdc;
    --band-grey: #c9c9c9;
  }
  * { margin: 0; padding: 0; box-sizing: border-box; }
  html, body { width: 1200px; height: 1200px; overflow: hidden; }
  body { background: var(--backdrop); position: relative; }

  .card {
    position: absolute;
    left: 244px;
    width: 712px;
    height: 417px;
    background: var(--card);
    overflow: hidden;
  }
  .card--front { top: 119px; }
  .card--back { top: 644px; }

  .brand-disc {
    position: absolute;
    border-radius: 50%;
    background: radial-gradient(circle at 40% 35%, #ffffff, var(--disc) 70%);
    border: 1px solid var(--disc-edge);
  }
  .brand-name {
    position: absolute;
    font-family: "Merriweather", serif;
    font-weight: 400;
    color: var(--green);
    text-transform: uppercase;
    white-space: nowrap;
  }
  .brand-name .line { display: block; }

  /* front */
  .card--front .brand-disc { left: 275px; top: 86px; width: 168px; height: 168px; }
  .card--front .brand-name { left: 0; right: 0; top: 270px; text-align: center; }
  .card--front .brand-name .main { font-size: 40px; letter-spacing: 1px; line-height: 46px; }
  .card--front .brand-name .sub { font-size: 12px; letter-spacing: 7px; line-height: 18px; }

  /* back */
  .card--back .brand-disc { left: 49px; top: 53px; width: 86px; height: 86px; }
  .card--back .brand-name { left: 166px; top: 68px; text-align: center; }
  .card--back .brand-name .main { font-size: 33px; letter-spacing: 1px; line-height: 38px; }
  .card--back .brand-name .sub { font-size: 10px; letter-spacing: 6px; line-height: 14px; }

  .holder { position: absolute; left: 41px; top: 192px; }
  .holder-name {
    font-family: "Merriweather", serif;
    font-weight: 700;
    font-size: 22px;
    color: var(--ink);
  }
  .holder-title {
    font-family: "Merriweather", serif;
    font-size: 15px;
    color: var(--ink-soft);
    margin-top: 4px;
  }

  .contact-list {
    position: absolute;
    left: 350px;
    top: 197px;
    list-style: none;
    font-family: "Lato", sans-serif;
    font-size: 17.5px;
    color: var(--ink);
  }
  .contact-list li { display: flex; align-items: center; height: 23px; }
  .contact-list svg { width: 16px; height: 16px; margin-right: 14px; fill: var(--green); flex: none; }

  .divider {
    position: absolute;
    left: 345px;
    right: 0;
    top: 320px;
    height: 2px;
    background: var(--green);
  }
  .address {
    position: absolute;
    left: 346px;
    top: 327px;
    font-family: "Lato", sans-serif;
    font-size: 17.5px;
    color: var(--ink);
  }
  .base-band {
    position: absolute;
    left: 0;
    bottom: 0;
    width: 100%;
    height: 17px;
  }
</style>
</head>
<body>

<section class="card card--front">
  <div class="brand-disc"></div>
  <div class="brand-name">
    <span class="line main">Veldtmoor</span>
    <span class="line sub">Capital Group</span>
  </div>
</section>

<section class="card card--back">
  <div class="brand-disc"></div>
  <div class="brand-name">
    <span class="line main">Veldtmoor</span>
    <span class="line sub">Capital Group</span>
  </div>

  <div class="holder">
    <p class="holder-name">Desmond Whitlake</p>
    <p class="holder-title">Managing Partner</p>
  </div>

  <ul class="contact-list">
    <li>
      <svg viewBox="0 0 16 16" aria-hidden="true"><path d="M2 6c0-2 3-3 6-3s6 1 6 3v1h-3V6H5v1H2z"/><path d="M4 8h8l1 6H3z"/></svg>
      415.555.0142
    </li>
    <li>
      <svg viewBox="0 0 16 16" aria-hidden="true"><rect x="4" y="1" width="8" height="4"/><rect x="1" y="6" width="14" height="6" rx="1"/><rect x="4" y="10" width="8" height="5"/></svg>
      415.555.0147
    </li>
    <li>
      <svg viewBox="0 0 16 16" aria-hidden="true"><path d="M4 0h8a1 1 0 0 1 1 1v14a1 1 0 0 1-1 1H4a1 1 0 0 1-1-1V1a1 1 0 0 1 1-1zm1 2v10h6V2z"/></svg>
      415.555.0193
    </li>
    <li>
      <svg viewBox="0 0 16 16" aria-hidden="true"><path d="M0 3h16v10H0z M1.5 4.5 8 9l6.5-4.5" fill="var(--green)"/><path d="M1 4l7 5 7-5" stroke="#fff" stroke-width="1.3" fill="none"/></svg>
      Desmond@veldtmoorcapital.ventures
    </li>
    <li>
      <svg viewBox="0 0 16 16" aria-hidden="true"><circle cx="8" cy="8" r="7"/><path d="M1 8h14M8 1c-3 3-3 11 0 14M8 1c3 3 3 11 0 14" stroke="#fff" stroke-width="1" fill="none"/></svg>
      www.veldtmoorcapital.ventures
    </li>
  </ul>

  <div class="divider"></div>
  <p class="address">187 Fenworth St San Francisco, CA 94187</p>

  <svg class="base-band" viewBox="0 0 712 17" preserveAspectRatio="none" aria-hidden="true">
    <defs>
      <linearGradient id="bandGreen" x1="0" x2="1">
        <stop offset="0" stop-color="var(--green)"/>
        <stop offset="1" stop-color="var(--green-light)"/>
      </linearGradient>
    </defs>
    <rect x="0" y="0" width="712" height="17" fill="var(--band-grey)"/>
    <polygon points="0,0 510,0 475,17 0,17" fill="url(#bandGreen)"/>
  </svg>
</section>

</body>
</html>
```